Stylish new business card needed!

Hello everyone! I am in need of a new business card design for an alarm company here in Hurricane WV. I have all fonts, color codes and logos provided for you use! We are a young company and like the style of a clean sleek looking business card. Would like it double sided, one side holding the logo and the other with your design!
Target Market(s)
The people that are looking for the newest tech for home automation and security
Industry/Entity Type
Alarm services; Home automation
Contact Information for Business Card
Name of person; position (Sales; Installer); Phone Number (555.418.7260); Employee cell Number; Website (www.GuardedByVelk.example); Employee Email; Double sided
Look and feel
Each slider illustrates characteristics of the customer's brand and the style your logo design should communicate.

```html
<!DOCTYPE html>
<html lang="en">
<head>
<meta charset="utf-8">
<title>Velk Business Card</title>
<link rel="stylesheet" href="https://fonts.googleapis.com/css2?family=Arimo:wght@400;700&display=swap">
<style>
  :root {
    --stage: #232323;
    --card-dark: #1f1f22;
    --orange: #f28c4f;
    --orange-deep: #e77a3a;
    --grey: #9a9a9c;
    --white: #ffffff;
    --emboss: #2a2a2e;
  }
  * { margin: 0; padding: 0; box-sizing: border-box; }
  html, body { width: 1200px; height: 780px; overflow: hidden; }
  body {
    background: var(--stage);
    font-family: "Arimo", Arial, sans-serif;
    position: relative;
  }
  .card {
    position: absolute;
    width: 520px;
    height: 297px;
    top: 242px;
    overflow: hidden;
  }
  .card--back { left: 50px; background: var(--orange); }
  .card--front { left: 630px; background: var(--card-dark); }

  /* back side */
  .back-pattern {
    position: absolute; inset: 0;
    background: linear-gradient(135deg, var(--orange) 0%, var(--orange-deep) 100%);
  }
  .back-mark {
    position: absolute; right: 70px; top: 120px;
    color: var(--white); font-weight: 700; font-size: 34px; letter-spacing: 2px;
  }

  /* front side */
  .front-deco {
    position: absolute; left: -18px; top: 148px;
    transform: rotate(90deg); transform-origin: left top;
    left: 92px; top: -6px;
    color: var(--emboss); font-weight: 700; font-size: 104px; letter-spacing: 6px;
  }
  .brand {
    position: absolute; right: 34px; top: 26px; text-align: right;
  }
  .brand__name {
    display: flex; align-items: center; justify-content: flex-end; gap: 10px;
    color: var(--grey); font-weight: 700; font-size: 58px; letter-spacing: 3px; line-height: 1;
  }
  .brand__dot { width: 16px; height: 16px; border-radius: 50%; background: var(--orange); }
  .brand__tagline {
    margin-top: 6px; color: var(--orange); font-weight: 700; font-size: 8px; letter-spacing: 0.8px;
  }
  .person {
    position: absolute; right: 18px; top: 138px;
    display: flex; align-items: stretch; gap: 10px;
  }
  .person__text { text-align: right; }
  .person__name { font-weight: 700; font-size: 25px; line-height: 1.05; }
  .person__first { color: var(--orange); }
  .person__last { color: var(--grey); }
  .person__role { color: var(--white); font-weight: 700; font-size: 14px; margin-top: 2px; }
  .person__bar { width: 14px; background: var(--orange); }
  .contacts {
    position: absolute; right: 18px; top: 200px; list-style: none; text-align: right;
  }
  .contacts li {
    display: flex; align-items: center; justify-content: flex-end; gap: 8px;
    color: var(--white); font-size: 13px; line-height: 19px;
  }
  .contacts svg { width: 12px; height: 12px; fill: var(--orange); }
</style>
</head>
<body>
  <section class="card card--back" aria-label="Card back">
    <div class="back-pattern" role="img" aria-label="Repeating embossed brand-name pattern in orange tones"></div>
    <div class="back-mark">VELK</div>
  </section>

  <section class="card card--front" aria-label="Card front">
    <div class="front-deco" aria-hidden="true">VELK</div>

    <div class="brand">
      <div class="brand__name"><span class="brand__dot"></span>VELK</div>
      <div class="brand__tagline">AUTOMATION AND SECURITY SERVICES</div>
    </div>

    <div class="person">
      <div class="person__text">
        <div class="person__name"><span class="person__first">Mara</span> <span class="person__last">Lindqvist</span></div>
        <div class="person__role">Sales; Installer</div>
      </div>
      <div class="person__bar"></div>
    </div>

    <ul class="contacts">
      <li>555.418.7260
        <svg viewBox="0 0 24 24"><path d="M6.6 10.8a15 15 0 0 0 6.6 6.6l2.2-2.2a1 1 0 0 1 1-.25 11.4 11.4 0 0 0 3.6.57 1 1 0 0 1 1 1V20a1 1 0 0 1-1 1A17 17 0 0 1 3 4a1 1 0 0 1 1-1h3.5a1 1 0 0 1 1 1c0 1.25.2 2.45.57 3.57a1 1 0 0 1-.25 1z"/></svg>
      </li>
      <li>555.302.9914
        <svg viewBox="0 0 24 24"><path d="M7 1h10a2 2 0 0 1 2 2v18a2 2 0 0 1-2 2H7a2 2 0 0 1-2-2V3a2 2 0 0 1 2-2zm0 3v15h10V4z"/></svg>
      </li>
      <li>www.GuardedByVelk.example
        <svg viewBox="0 0 24 24"><path d="M12 2a10 10 0 1 0 0 20 10 10 0 0 0 0-20zm6.9 6h-3a15 15 0 0 0-1.3-3.9A8 8 0 0 1 18.9 8zM12 4a13 13 0 0 1 1.9 4h-3.8A13 13 0 0 1 12 4zM4.3 14a8 8 0 0 1 0-4h3.4a16 16 0 0 0 0 4zm.8 2h3a15 15 0 0 0 1.3 3.9A8 8 0 0 1 5.1 16zm3-8h-3a8 8 0 0 1 4.3-3.9A15 15 0 0 0 8.1 8zM12 20a13 13 0 0 1-1.9-4h3.8A13 13 0 0 1 12 20zm2.3-6H9.7a14 14 0 0 1 0-4h4.6a14 14 0 0 1 0 4zm.3 5.9a15 15 0 0 0 1.3-3.9h3a8 8 0 0 1-4.3 3.9zm1.7-5.9a16 16 0 0 0 0-4h3.4a8 8 0 0 1 0 4z"/></svg>
      </li>
      <li>info@GuardedByVelk.example
        <svg viewBox="0 0 24 24"><path d="M2 5h20v14H2zm2 2v.5l8 5 8-5V7zm0 2.8V17h16V9.8l-8 5z"/></svg>
      </li>
    </ul>
  </section>
</body>
</html>
```